New Organic Skin Care Line Needs to Design a Product Label

***THE WINNER OF THIS PROJECT WILL MOST LIKELY BECOME THE EXCLUSIVE DESIGNER FOR OUR OTHER PRODUCT LABELS***

We need a label design for a new organic skin care product line called "Maple Dew Gala." This specific product is a 100% pure organic coconut oil. It's used for skin hydration, protection, and makeup removal.

Info to include on front label:

1. Logo: Maple Dew Gala (attached)
2. Product Name: Pure Coconut Oil (emphasize "organic" somewhere)
3. Slogan: Hydrate your skin and hair.
4. Size: 8 FL OZ 236mL

Attached is:

1. The brand logo "Maple Dew Gala" with a white background.
2. An image of the bottle we will use.
3. An image of the bottle with lines to show the size and placement of the label.
4. The brand logo "Maple Dew Gala" with a black background. (photoshop file)

What we need:

A simple mock up of the front side of the label on the bottle. We first want to know what it will look like on the bottle given the size and dimensions.

- We would like one label with a white background (including the logo with a white background).
- We would like a second label with a black background (including the logo with a black background, just need to make the black font white instead of black).

We can get a great idea of what to expect from the front side of the label so we will complete the back side once we identify a winner.
Updates

Apologies, but we are now using a different bottle. The previous one is now discontinued. Please view the two most recent images uploaded. One is an image of the new bottle by itself. The other is an image of that bottle with instructions. Please use your most recent designs on the new bottle. Feel free to make any modifications you see fit to compliment the new bottle shape. Added Friday, March 18, 2016

Reason: We are still working with the label company to finalize the size. Once the size is confirmed we will have to tweak labels based on finalized measurements.

Target Market(s)

Women, 18-70

Industry/Entity Type

Skin Care Product

Font styles to use
Decorative
Script

Requirements
Must have
• -"shabby sheek" and "cute" theme
• -soft organic feel
• -the ingredients are organic, pure, and natural. That should be an essence of the label.

```html
<!DOCTYPE html>
<html lang="en">
<head>
<meta charset="utf-8">
<title>Maple Dew Gala – Pure Coconut Oil Labels</title>
<link href="https://fonts.googleapis.com/css2?family=Cinzel:wght@400;700&family=Macondo&display=swap" rel="stylesheet">
<style>
  :root {
    --canvas: #ffffff;
    --label-dark: #000000;
    --label-light: #ffffff;
    --rose-pink: #e8247f;
    --rose-deep: #b01563;
    --rose-pale: #f7c6dc;
    --ink-dark: #1a1a1a;
    --ink-light: #ffffff;
  }
  * { margin: 0; padding: 0; box-sizing: border-box; }
  html, body {
    width: 1200px;
    height: 1000px;
    overflow: hidden;
    background: var(--canvas);
  }
  .label-set {
    position: absolute;
    top: 244px;
    left: 0;
    width: 1200px;
    height: 512px;
    display: flex;
  }
  .label {
    position: relative;
    width: 600px;
    height: 512px;
    text-align: center;
  }
  .label--dark { background: var(--label-dark); color: var(--ink-light); }
  .label--light { background: var(--label-light); color: var(--ink-dark); }

  .label__roses {
    position: absolute;
    left: 0;
    top: 40px;
    width: 600px;
    height: 230px;
  }
  .label__brand {
    position: absolute;
    left: 0;
    width: 100%;
    font-family: "Cinzel", serif;
    font-size: 21px;
    letter-spacing: 4px;
    display: flex;
    justify-content: center;
    align-items: center;
    gap: 12px;
  }
  .label__brand-dot {
    width: 10px;
    height: 10px;
    border-radius: 50%;
    background: var(--rose-pink);
  }
  .label__slogan {
    position: absolute;
    left: 0;
    width: 100%;
    font-family: "Macondo", cursive;
    font-size: 18px;
    color: var(--rose-pink);
  }
  .label__details {
    position: absolute;
    left: 0;
    width: 100%;
    font-family: "Cinzel", serif;
    line-height: 1.1;
  }
  .label__organic { font-weight: 700; font-size: 15px; }
  .label__product { font-size: 15px; }
  .label__size { font-size: 11px; }

  .label--dark .label__brand { top: 322px; }
  .label--dark .label__slogan { top: 347px; }
  .label--dark .label__details { top: 382px; }
  .label--light .label__brand { top: 333px; }
  .label--light .label__slogan { top: 358px; }
  .label--light .label__details { top: 393px; }
</style>
</head>
<body>
  <main class="label-set">
    <section class="label label--dark">
      <svg class="label__roses" viewBox="0 0 600 230" role="img" aria-label="Arch of hand-drawn pink and white roses">
        <defs>
          <linearGradient id="roses-dark" x1="0" y1="0" x2="1" y2="0">
            <stop offset="0" stop-color="#e8247f"/>
            <stop offset="0.35" stop-color="#f4f0f2"/>
            <stop offset="0.5" stop-color="#e8247f"/>
            <stop offset="1" stop-color="#f4f0f2"/>
          </linearGradient>
        </defs>
        <path d="M20 170 C40 110 90 80 110 60 C150 20 210 0 270 10 C330 20 380 20 440 40 C500 60 570 100 585 180 C570 215 520 225 480 210 C450 160 380 120 300 110 C220 110 150 140 120 200 C80 225 30 215 20 170 Z" fill="url(#roses-dark)"/>
      </svg>
      <h1 class="label__brand">Maple Dew Gala<span class="label__brand-dot"></span></h1>
      <p class="label__slogan">Hydrate your skin and hair.</p>
      <div class="label__details">
        <p class="label__organic">Organic</p>
        <p class="label__product">Pure Coconut Oil</p>
        <p class="label__size">8 FL OZ 236mL</p>
      </div>
    </section>

    <section class="label label--light">
      <svg class="label__roses" viewBox="0 0 600 230" role="img" aria-label="Arch of hand-drawn pink rose outlines and filled pink roses">
        <defs>
          <linearGradient id="roses-light" x1="0" y1="0" x2="1" y2="0">
            <stop offset="0" stop-color="#c81c6c"/>
            <stop offset="0.3" stop-color="#f7c6dc"/>
            <stop offset="0.48" stop-color="#e02878"/>
            <stop offset="1" stop-color="#f7c6dc"/>
          </linearGradient>
        </defs>
        <path d="M5 170 C20 110 70 80 90 60 C140 15 210 0 280 5 C340 15 390 20 450 40 C520 60 585 110 595 190 C575 220 520 228 480 212 C450 165 380 125 300 115 C220 115 150 145 130 200 C80 225 15 215 5 170 Z" fill="url(#roses-light)"/>
      </svg>
      <h1 class="label__brand">Maple Dew Gala<span class="label__brand-dot"></span></h1>
      <p class="label__slogan">Hydrate your skin and hair.</p>
      <div class="label__details">
        <p class="label__organic">Organic</p>
        <p class="label__product">Pure Coconut Oil</p>
        <p class="label__size">8 FL OZ 236mL</p>
      </div>
    </section>
  </main>
</body>
</html>
```